Verodex business card

Business card for sustainable investment company called "Verodex". Verodex is an exchange platform selling carbon credits between buyers and sellers. Carbon Credits are an environmental commodity for reducing global carbon emissions.

the card should obviously have our logo and the theme should be sustainability/environment mixed with a trading platform.

Contact Information for Business Card

Logo, Name, Title, Phone, Email

Colors
0054AA
0677BA
7BADD7
CADEEF
E8F1F8
0094D4
00A9DD
6FCCEA
C7EBF8
E9F6FB
00AB8E
00BBA5
67D7C9
C6EFE9
E9F9F6
59FF00
82FF00
B8FF75
E3FFCB
F4FFEA

```html
<!DOCTYPE html>
<html lang="en">
<head>
<meta charset="utf-8">
<title>Verodex business card</title>
<link href="https://fonts.googleapis.com/css2?family=Arimo:wght@400;700&display=swap" rel="stylesheet">
<style>
  :root {
    --backdrop: #2e2e2e;
    --card: #000000;
    --cyan: #2ee8ec;
    --blue: #2a78ea;
    --navy: #243955;
    --white: #ffffff;
  }
  * { margin: 0; padding: 0; box-sizing: border-box; }
  html, body {
    width: 1200px;
    height: 1015px;
    overflow: hidden;
    background: var(--backdrop);
    font-family: "Arimo", Arial, sans-serif;
  }
  .sheet {
    position: relative;
    width: 1200px;
    height: 1015px;
  }
  .card {
    position: absolute;
    left: 240px;
    width: 720px;
    height: 420px;
    background: var(--card);
    box-shadow: 0 10px 24px rgba(0,0,0,0.45);
    overflow: hidden;
  }
  .card--front { top: 60px; }
  .card--back { top: 535px; }
  .card__rule {
    position: absolute;
    left: 0;
    right: 0;
    bottom: 0;
    height: 7px;
    background: linear-gradient(90deg, var(--cyan), var(--blue));
  }
  .brand {
    position: absolute;
    display: flex;
    align-items: center;
  }
  .brand__dot {
    border-radius: 50%;
    background: var(--blue);
    flex: none;
  }
  .brand__name {
    font-weight: 700;
    letter-spacing: 0.04em;
  }
  .card--front .brand {
    left: 0; right: 0; top: 170px;
    justify-content: center;
    gap: 22px;
  }
  .card--front .brand__dot { width: 44px; height: 44px; }
  .card--front .brand__name {
    font-size: 62px;
    color: var(--navy);
  }
  .card--back .brand {
    right: 56px; top: 66px;
    gap: 18px;
  }
  .card--back .brand__dot { width: 64px; height: 64px; }
  .card--back .brand__name {
    font-size: 46px;
    color: var(--blue);
  }
  .contact {
    position: absolute;
    left: 70px;
    top: 200px;
    color: var(--white);
  }
  .contact__name {
    font-size: 30px;
    font-weight: 700;
    letter-spacing: 0.01em;
    background: linear-gradient(90deg, var(--cyan), var(--blue));
    -webkit-background-clip: text;
    background-clip: text;
    color: transparent;
  }
  .contact__title {
    font-size: 17px;
    margin-top: 4px;
    letter-spacing: 0.02em;
  }
  .contact__divider {
    width: 150px;
    height: 1px;
    margin: 20px 0 18px 30px;
    background: linear-gradient(90deg, var(--cyan), var(--blue));
  }
  .contact__list { list-style: none; }
  .contact__item {
    display: flex;
    align-items: center;
    gap: 10px;
    font-size: 22px;
    line-height: 30px;
  }
  .contact__item:nth-child(2) { padding-left: 16px; }
  .contact__item:nth-child(3) { padding-left: 32px; }
  .contact__icon { width: 20px; height: 20px; flex: none; }
</style>
</head>
<body>
<main class="sheet">
  <section class="card card--front" aria-label="Card front">
    <div class="brand">
      <span class="brand__dot"></span>
      <span class="brand__name">VERODEX</span>
    </div>
    <div class="card__rule"></div>
  </section>

  <section class="card card--back" aria-label="Card back">
    <div class="brand">
      <span class="brand__dot"></span>
      <span class="brand__name">VERODEX</span>
    </div>

    <div class="contact">
      <p class="contact__name">MARCUS ELLERY</p>
      <p class="contact__title">MANAGING DIRECTOR</p>
      <div class="contact__divider"></div>
      <ul class="contact__list">
        <li class="contact__item">
          <svg class="contact__icon" viewBox="0 0 24 24" aria-hidden="true">
            <path d="M6.6 10.8a15 15 0 0 0 6.6 6.6l2.2-2.2a1 1 0 0 1 1-.25 11.4 11.4 0 0 0 3.6.6 1 1 0 0 1 1 1V20a1 1 0 0 1-1 1A17 17 0 0 1 3 4a1 1 0 0 1 1-1h3.5a1 1 0 0 1 1 1c0 1.25.2 2.45.6 3.6a1 1 0 0 1-.25 1z" fill="#2ec4ee"/>
          </svg>
          044-555 210 347
        </li>
        <li class="contact__item">
          <svg class="contact__icon" viewBox="0 0 24 24" aria-hidden="true">
            <rect x="2" y="5" width="20" height="14" rx="1" fill="#2ab0ee"/>
            <path d="M2.5 5.5 12 13l9.5-7.5" fill="none" stroke="#000" stroke-width="1.6"/>
          </svg>
          hello@verodex.net
        </li>
        <li class="contact__item">
          <svg class="contact__icon" viewBox="0 0 24 24" aria-hidden="true">
            <g fill="none" stroke="#2a90ec" stroke-width="1.8">
              <circle cx="12" cy="12" r="9.5"/>
              <ellipse cx="12" cy="12" rx="4.2" ry="9.5"/>
              <path d="M2.5 12h19M4 7h16M4 17h16"/>
            </g>
          </svg>
          www.verodex.net
        </li>
      </ul>
    </div>
    <div class="card__rule"></div>
  </section>
</main>
</body>
</html>
```